Talvex Health Artificial Intelligence MedTech Software Website Refresh

We need a new website (old one at www.talvex-health.example is no longer relevant) for our medtech software company using artificial intelligence to deliver higher quality, faster and more cost effective care in oncology. The audiences are both healthcare providers and health insurance payers. We've created an extensive outline to follow and have the old site still live for easy content use and repurposing. Our primary need is a great overhaul to look and feel. If we find a successful designer, we will need additional work done for graphics and other presentation projects.

Target Market(s)

Health care providers (doctors) and administrators plus health insurers

Industry/Entity Type

Medtech

Coding

Number of Pages Required

5+ page

Font styles to use
Other font styles liked:
• Roboto see Style Guide

Requirements
Must have
• See attached brief
Nice to have
• See attached brief. We like www.caremint.example and www.lumoradx.example as sites.
Should not have
• See attached brief

```html
<!DOCTYPE html>
<html lang="en">
<head>
<meta charset="utf-8">
<title>Talvex Health</title>
<link href="https://fonts.googleapis.com/css2?family=Roboto:wght@400;500;700&display=swap" rel="stylesheet">
<style>
:root{
  --blue:#2a93d8;
  --blue-deep:#1565b6;
  --navy:#0d2a52;
  --band:#1663b0;
  --ink:#111;
  --muted:#555;
  --soft:#efefef;
  --line:#d9d9d9;
  --white:#fff;
}
*{box-sizing:border-box;margin:0;padding:0}
html,body{width:1200px;height:3446px;overflow:hidden}
body{font-family:'Roboto',sans-serif;color:var(--ink);background:var(--white);position:relative}
.abs{position:absolute}
/* hero */
.hero{position:absolute;left:0;top:0;width:1200px;height:654px;background:linear-gradient(100deg,#1a6fc4 0%,#2487d6 55%,#2e9ee0 100%);color:var(--white)}
.brand{position:absolute;left:110px;top:48px;display:flex;align-items:center;gap:12px;font-weight:700;font-size:44px;color:var(--white)}
.brand .dot{width:22px;height:22px;border-radius:50%;background:#7cc6f2}
.nav{position:absolute;right:110px;top:60px;display:flex;gap:27px;font-size:15px;font-weight:500}
.nav a{color:var(--white);text-decoration:none}
.nav a.active{color:#6cc0f0;border-bottom:2px solid #6cc0f0;padding-bottom:6px}
.hero h1{position:absolute;left:110px;top:196px;font-size:50px;font-weight:700;letter-spacing:.5px}
.hero .lead{position:absolute;left:110px;top:268px;width:500px;font-size:15px;font-weight:500;line-height:24px}
.hero ul{position:absolute;left:110px;top:355px;width:500px;list-style:none;font-size:13.5px;line-height:21.5px}
.hero li{position:relative;padding-left:26px;margin-bottom:16px}
.hero li svg{position:absolute;left:0;top:4px}
.photo{position:absolute;width:140px;height:140px;border-radius:50%;border:3px solid rgba(255,255,255,.5)}
/* headings */
.sec-title{position:absolute;left:0;width:1200px;text-align:center;font-size:38px;font-weight:700}
.sec-title span{color:var(--blue-deep)}
/* solution circles */
.bubble{position:absolute;width:222px;height:222px;border-radius:50%;display:flex;flex-direction:column;align-items:center;justify-content:center;color:var(--white);text-align:center}
.bubble .ico{width:46px;height:46px;border-radius:8px;background:rgba(255,255,255,.25);margin-bottom:12px}
.bubble b{font-size:18px;font-weight:500;margin-bottom:8px}
.bubble small{font-size:15px;line-height:22px;width:160px}
.patient{left:489px;top:844px;background:var(--blue)}
.payer{left:222px;top:1111px;background:var(--navy)}
.provider{left:755px;top:1111px;background:var(--blue-deep)}
.core{left:489px;top:1111px;background:var(--white);box-shadow:0 6px 24px rgba(0,0,0,.12);color:var(--blue-deep);font-weight:700;font-size:26px;gap:0}
/* features */
.feature{position:absolute;top:1391px;width:230px;text-align:center}
.feature .ico{width:100px;height:100px;border-radius:50%;background:#ececec;margin:0 auto 22px}
.feature h3{font-size:17px;font-weight:500;margin-bottom:16px}
.feature p{font-size:13.5px;color:var(--muted);line-height:21px}
.btn{position:absolute;left:505px;top:1655px;width:190px;height:46px;border-radius:23px;background:var(--blue);color:var(--white);font-size:16px;font-weight:500;display:flex;align-items:center;justify-content:center}
/* cards */
.card{position:absolute;top:1876px;width:313px;height:362px;border:1px solid #dcdcdc;background:var(--white)}
.card .img{height:207px}
.card h4{margin:22px 24px 0;font-size:16px;font-weight:500;line-height:22px;height:44px}
.card .meta{margin:10px 24px 0;font-size:13px;color:#888;display:flex;align-items:center;gap:6px;padding-bottom:14px;border-bottom:1px solid var(--line)}
.card .dl{margin:14px 24px 0;font-size:14.5px;color:var(--blue-deep);font-weight:500;display:flex;align-items:center;gap:8px}
/* partners */
.partners{position:absolute;left:0;top:2363px;width:1200px;height:411px;background:var(--soft)}
.partners h2{position:absolute;left:0;top:52px;width:1200px;text-align:center;font-size:38px;font-weight:500}
.partners h2 span{color:var(--blue-deep)}
.p-name{position:absolute;width:210px;text-align:center;font-size:17px;font-weight:700;color:#3a4a6b;display:flex;align-items:center;justify-content:center;gap:8px;height:60px}
.p-name i{width:14px;height:14px;background:#3a4a6b;display:inline-block;flex:none}
.vline{position:absolute;width:1px;background:#d4d4d4}
/* contact */
.contact{position:absolute;left:0;top:2774px;width:1200px;height:321px;background:var(--band);color:var(--white)}
.contact h2{position:absolute;left:0;top:44px;width:1200px;text-align:center;font-size:38px;font-weight:500}
.c-col{position:absolute;top:127px;width:240px;text-align:center}
.c-col .ic{width:54px;height:54px;border-radius:50%;background:var(--blue);margin:0 auto 16px;display:flex;align-items:center;justify-content:center}
.c-col b{display:block;font-size:15px;font-weight:500;margin-bottom:10px}
.c-col p{font-size:14px;line-height:21px}
/* footer */
.f-brand{position:absolute;left:110px;top:3195px;display:flex;align-items:center;gap:10px;font-size:40px;font-weight:700;color:var(--blue-deep)}
.f-brand .dot{width:20px;height:20px;border-radius:50%;background:var(--blue)}
.social{position:absolute;top:3296px;width:36px;height:36px;border-radius:50%;border:1.5px solid #444}
.f-col{position:absolute;top:3165px;font-size:13.5px;color:#666}
.f-col h5{font-size:16px;font-weight:500;color:var(--ink);margin-bottom:18px}
.f-col li{list-style:none;line-height:26px}
.f-item{position:relative;padding-left:24px;margin-bottom:12px;line-height:19px}
.f-item b{display:block;color:var(--ink);font-size:12px;font-weight:500}
.f-item svg{position:absolute;left:0;top:2px}
.rule{position:absolute;left:110px;top:3395px;width:980px;height:1px;background:#ccc}
.copy{position:absolute;left:0;top:3412px;width:1200px;text-align:center;font-size:13px;color:#555}
</style>
</head>
<body>

<header class="hero">
  <div class="brand"><span>Talvex Health</span><span class="dot"></span></div>
  <nav class="nav">
    <a class="active">Home</a><a>Solutions</a><a>Clinical Evidence</a><a>About</a><a>Contact Us</a>
  </nav>
  <h1>TALVEX HEALTH, INC.</h1>
  <p class="lead">Talvex Health, Inc. is an expert team with the vision of improving oncology treatment delivery, patient outcomes and cost effectiveness through the power of AI.</p>
  <ul>
    <li><svg width="13" height="13" viewBox="0 0 13 13"><circle cx="6.5" cy="6.5" r="6.5" fill="#fff"/><path d="M3.5 6.7l2 2 4-4" stroke="#1f7ccc" stroke-width="1.8" fill="none"/></svg>The problem(s) for providers: creating a treatment directive starts from scratch for every patient and is a time consuming iterative/back and forth process . Further, because there is little transparency to communicate patient-specific treatment needs to the payer, prior authorization is a burden.</li>
    <li><svg width="13" height="13" viewBox="0 0 13 13"><circle cx="6.5" cy="6.5" r="6.5" fill="#fff"/><path d="M3.5 6.7l2 2 4-4" stroke="#1f7ccc" stroke-width="1.8" fill="none"/></svg>The problem for payers: there is no transparency to the uniqueness of the patient<br>so the process has costly delays to gather more information and align the treatment to what's best for the patient; often attempts to redirect care are</li>
  </ul>
  <div class="photo" style="left:834px;top:136px;background:linear-gradient(160deg,#e9d7c8,#b9c8d6)" role="img" aria-label="Smiling patient wearing a head wrap"></div>
  <div class="photo" style="left:667px;top:303px;background:linear-gradient(160deg,#f1ece8,#cbb8a8)" role="img" aria-label="Caregiver holding a patient's hand"></div>
  <div class="photo" style="left:834px;top:303px;background:linear-gradient(160deg,#c9c9c9,#8f9296)" role="img" aria-label="Patient in grey top"></div>
  <div class="photo" style="left:1002px;top:303px;background:linear-gradient(160deg,#e8eef2,#a9b6bf)" role="img" aria-label="Patient resting in a clinic"></div>
  <div class="photo" style="left:834px;top:471px;background:linear-gradient(160deg,#efe3d9,#c9ad96)" role="img" aria-label="Close-up of hands in care"></div>
</header>

<h2 class="sec-title" style="top:758px">TALVEX HEALTH <span>HAS SOLUTIONS</span></h2>

<div class="bubble patient"><div class="ico" role="img" aria-label="Patient icon"></div><b>Patient</b><small>30% reduction in side effects</small></div>
<div class="bubble payer"><div class="ico" role="img" aria-label="Payer icon"></div><b>Payer</b><small>$15M PMPY</small></div>
<div class="bubble core">Talvex Health</div>
<div class="bubble provider"><div class="ico" role="img" aria-label="Provider icon"></div><b>Provider</b><small>$4K/Patient</small></div>

<div class="feature" style="left:83px"><div class="ico" role="img" aria-label="Connected systems icon"></div><h3>Integrated</h3><p>Integrated into MD clinical workflows and IT systems</p></div>
<div class="feature" style="left:344px"><div class="ico" role="img" aria-label="AI chip icon"></div><h3>Automated PA</h3><p>Automated PA removing manual processes, saving administrative costs</p></div>
<div class="feature" style="left:606px"><div class="ico" role="img" aria-label="Quality dashboard icon"></div><h3>Improved care quality</h3><p>Improved care quality equal or better personalized care</p></div>
<div class="feature" style="left:868px"><div class="ico" role="img" aria-label="Financial report icon"></div><h3>Financial gains</h3><p>Financial gains through reduced write-offs and right-sized care</p></div>

<div class="btn">Request A Demo</div>

<h2 class="sec-title" style="top:1796px">CLINICAL <span>EVIDENCE</span></h2>

<article class="card" style="left:111px">
  <div class="img" role="img" aria-label="Clinician holding a phone with AI health graphics" style="background:linear-gradient(135deg,#3f74b0,#9db6cf)"></div>
  <h4>AI power saves time and improves treatment plan quality</h4>
  <div class="meta"><svg width="11" height="11" viewBox="0 0 11 11"><rect x=".5" y="1.5" width="10" height="9" fill="none" stroke="#999"/><path d="M.5 4h10" stroke="#999"/></svg>Dec 10, 2020 &nbsp;|&nbsp; <svg width="10" height="11" viewBox="0 0 10 11"><circle cx="5" cy="3" r="2.5" fill="#999"/><path d="M0 11c0-3 2-4.5 5-4.5s5 1.5 5 4.5z" fill="#999"/></svg>Sam Avery</div>
  <div class="dl"><svg width="12" height="14" viewBox="0 0 12 14"><path d="M1 1h7l3 3v9H1z" fill="none" stroke="#1565b6" stroke-width="1.3"/></svg>DownLoad Now</div>
</article>
<article class="card" style="left:443px">
  <div class="img" role="img" aria-label="Doctor reviewing scans on digital screens" style="background:linear-gradient(135deg,#8fa7c3,#2a3f7a)"></div>
  <h4>Leveraging Artificial Intelligence (AI) clinical decision support</h4>
  <div class="meta"><svg width="11" height="11" viewBox="0 0 11 11"><rect x=".5" y="1.5" width="10" height="9" fill="none" stroke="#999"/><path d="M.5 4h10" stroke="#999"/></svg>Dec 10, 2020 &nbsp;|&nbsp; <svg width="10" height="11" viewBox="0 0 10 11"><circle cx="5" cy="3" r="2.5" fill="#999"/><path d="M0 11c0-3 2-4.5 5-4.5s5 1.5 5 4.5z" fill="#999"/></svg>Sam Avery</div>
  <div class="dl"><svg width="12" height="14" viewBox="0 0 12 14"><path d="M1 1h7l3 3v9H1z" fill="none" stroke="#1565b6" stroke-width="1.3"/></svg>DownLoad Now</div>
</article>
<article class="card" style="left:776px">
  <div class="img" role="img" aria-label="Surgeons working in an operating room" style="background:linear-gradient(135deg,#5f8fb3,#b9d3e0)"></div>
  <h4>Implementation and impact of AI decision support software</h4>
  <div class="meta"><svg width="11" height="11" viewBox="0 0 11 11"><rect x=".5" y="1.5" width="10" height="9" fill="none" stroke="#999"/><path d="M.5 4h10" stroke="#999"/></svg>Dec 10, 2020 &nbsp;|&nbsp; <svg width="10" height="11" viewBox="0 0 10 11"><circle cx="5" cy="3" r="2.5" fill="#999"/><path d="M0 11c0-3 2-4.5 5-4.5s5 1.5 5 4.5z" fill="#999"/></svg>Sam Avery</div>
  <div class="dl"><svg width="12" height="14" viewBox="0 0 12 14"><path d="M1 1h7l3 3v9H1z" fill="none" stroke="#1565b6" stroke-width="1.3"/></svg>DownLoad Now</div>
</article>

<section class="partners">
  <h2>Our <span>Partners</span></h2>
  <div class="vline" style="left:355px;top:140px;height:180px"></div>
  <div class="vline" style="left:654px;top:140px;height:180px"></div>
  <div class="vline" style="left:843px;top:140px;height:180px"></div>
  <div class="abs" style="left:110px;top:226px;width:980px;height:1px;background:#d4d4d4"></div>
  <div class="p-name" style="left:110px;top:140px;justify-content:flex-start"><i></i>Lakeshore Medicine</div>
  <div class="p-name" style="left:400px;top:140px">Hollowbrook Health</div>
  <div class="p-name" style="left:645px;top:140px;width:210px">Bayview Univ. Health</div>
  <div class="p-name" style="left:880px;top:140px;justify-content:flex-end">Southridge Cancer Center</div>
  <div class="p-name" style="left:110px;top:250px;justify-content:flex-start"><i></i>Meridian Crest Health</div>
  <div class="p-name" style="left:400px;top:250px">Ashgrove Cancer Institute</div>
  <div class="p-name" style="left:645px;top:250px;width:210px">Eastport General</div>
  <div class="p-name" style="left:880px;top:250px;justify-content:flex-end">Kestrel Women's Hospital</div>
</section>

<section class="contact">
  <h2>Contact Us</h2>
  <div class="c-col" style="left:90px"><div class="ic"><svg width="16" height="22" viewBox="0 0 16 22"><path d="M8 0a8 8 0 0 1 8 8c0 6-8 14-8 14S0 14 0 8a8 8 0 0 1 8-8z" fill="#fff"/><circle cx="8" cy="8" r="3" fill="#2a93d8"/></svg></div><b>California Address</b><p>480 Harbor Lane, Suite<br>310 Redwood Shores, CA 94065</p></div>
  <div class="c-col" style="left:351px"><div class="ic"><svg width="16" height="22" viewBox="0 0 16 22"><path d="M8 0a8 8 0 0 1 8 8c0 6-8 14-8 14S0 14 0 8a8 8 0 0 1 8-8z" fill="#fff"/><circle cx="8" cy="8" r="3" fill="#2a93d8"/></svg></div><b>Boston Address</b><p>27 Quarry Street Second Floor<br>Millbrook, MA 01890</p></div>
  <div class="c-col" style="left:613px"><div class="ic"><svg width="20" height="20" viewBox="0 0 20 20"><path d="M4 1l4 4-2 3c1 3 3 5 6 6l3-2 4 4-3 3C8 19 1 12 1 4z" fill="#fff"/></svg></div><b>Phone</b><p>(555) 014-2290</p></div>
  <div class="c-col" style="left:874px"><div class="ic"><svg width="20" height="15" viewBox="0 0 20 15"><rect width="20" height="15" rx="2" fill="#fff"/><path d="M1 2l9 7 9-7" stroke="#2a93d8" stroke-width="1.8" fill="none"/></svg></div><b>Email</b><p>info@talvex-health.example<br>support@talvex-health.example</p></div>
</section>

<div class="f-brand"><span>Talvex</span><span class="dot"></span></div>
<div class="social" style="left:122px"></div>
<div class="social" style="left:165px"></div>
<div class="social" style="left:209px"></div>
<div class="social" style="left:252px"></div>

<div class="f-col" style="left:415px">
  <h5>Our Office Address</h5>
  <div class="f-item"><svg width="12" height="12" viewBox="0 0 20 20"><path d="M4 1l4 4-2 3c1 3 3 5 6 6l3-2 4 4-3 3C8 19 1 12 1 4z" fill="#2a93d8"/></svg><b>Phone</b>(555) 014-2290</div>
  <div class="f-item"><svg width="13" height="10" viewBox="0 0 20 15"><rect width="20" height="15" rx="2" fill="#2a93d8"/></svg><b>Email</b>info@talvex-health.example</div>
  <div class="f-item"><svg width="10" height="14" viewBox="0 0 16 22"><path d="M8 0a8 8 0 0 1 8 8c0 6-8 14-8 14S0 14 0 8a8 8 0 0 1 8-8z" fill="#2a93d8"/></svg><b>Location</b>480 Harbor Lane Suite 310<br>Redwood Shores, CA 94065</div>
</div>
<div class="f-col" style="left:755px">
  <h5>Company</h5>
  <ul><li>Home</li><li>Solutions</li><li>Clinical Evidence</li><li>About</li><li>Contact Us</li></ul>
</div>
<div class="f-col" style="left:965px">
  <h5>Information</h5>
  <ul><li>Terms &amp; Conditions</li><li>Privacy Policy</li><li>Disclaimer</li><li>Site Map</li><li>Customer Support</li></ul>
</div>

<div class="rule"></div>
<p class="copy">Copyrights ©talvex-health 2020 | Allrights Reserved</p>

</body>
</html>
```